Marwick Biomedical Research Institute (MBRI) Web Design

MBRI is a non-profit organization focused on saving the lives of terminally ill patients by becoming the leaders in cutting-edge research, innovative technologies, utilizing national and international partnerships as well as the associated allopathic and naturopathic treatments necessary to do so.

Our primary focus is raising funds to support the research and acquisition of new technologies for life saving treatments which are NOT a one size fits all approach like conventional medicine but rather a marriage of the latest technologies used in combination with other new treatment possibilities for a successful end result.

Our domain is marwickbri.org

Logo files are attached.

Looking for something clean, light, healthy.

Target Market(s)

The site should look and feel towards research/scientific grant writing.
Medical professionals, Medical Scientists.

Industry/Entity Type

Medical And Science

Number of Pages Required

4 page

Requirements
Nice to have
• Here are examples of sites I like in the order of how much I like them.
• https://www.palvorn.org/give.html
• https://www.thekqtf.org/donate-to-kqtf
• https://www.veltrasound.org/we-are-vsf/join-the-cause
• https://www.orvenly.org/involved/donate.html
• https://give.zdkt.org/checkout/donation?eid=58217
• https://www.quimbrel.org/how-you-can-help
• https://donate3.orvenly.org/

```html
<!DOCTYPE html>
<html lang="en">
<head>
<meta charset="utf-8">
<title>MBRI — Marwick Biomedical Research Institute</title>
<link href="https://fonts.googleapis.com/css2?family=Open+Sans:wght@400;600;700&display=swap" rel="stylesheet">
<style>
:root{
  --blue:#1670b3;
  --green:#5aa531;
  --title-blue:#1f76b8;
  --ink:#333;
  --muted:#666;
  --grey-bg:#f2f2f2;
  --footer:#363636;
  --footer-text:#b7b7b7;
  --white:#fff;
}
*{box-sizing:border-box;margin:0;padding:0}
html,body{width:1200px;height:3152px;overflow:hidden}
body{font-family:"Open Sans",Arial,sans-serif;color:var(--ink);background:var(--white);position:relative}
a{color:inherit;text-decoration:none}

.site-header{position:absolute;top:0;left:0;width:1200px;height:132px}
.brand{position:absolute;left:132px;top:50px;font-size:20px;font-weight:600;color:var(--ink);line-height:30px}
.header-actions{position:absolute;top:40px;right:132px;display:flex;gap:12px}
.btn-top{height:38px;padding:0 18px;display:flex;align-items:center;gap:8px;color:#fff;font-size:13px;font-weight:600}
.btn-login{background:var(--blue)}
.btn-donate{background:var(--green)}

.main-nav{position:absolute;top:132px;left:0;width:1200px;height:40px;background:var(--blue)}
.main-nav ul{list-style:none;display:flex;margin-left:132px;height:40px}
.main-nav li{height:40px;padding:0 29px;display:flex;align-items:center;color:#fff;font-size:13px;font-weight:600;text-transform:uppercase}
.main-nav li.active{background:var(--green)}

.hero{position:absolute;top:172px;left:0;width:1200px;height:442px;background:linear-gradient(90deg,#dfe6ec 0%,#f3f5f7 35%,#e8d7cb 55%,#eef1f4 75%,#dde4ea 100%)}
.slider-arrow{position:absolute;width:28px;height:28px;background:#6d6d6d;display:flex;align-items:center;justify-content:center}

.section-title{font-size:34px;font-weight:600;text-align:center;text-transform:uppercase}
.welcome{position:absolute;top:614px;left:0;width:1200px;height:285px}
.welcome .section-title{color:var(--green);margin-top:70px}
.welcome p{width:936px;margin:12px auto 0;font-size:12.5px;line-height:21px;color:var(--muted);text-align:center}

.services{position:absolute;top:899px;left:0;width:1200px;height:607px;background:var(--grey-bg)}
.services .section-title{color:var(--title-blue);margin-top:70px}
.card{position:absolute;top:132px;width:296px;height:404px;background:#fff;box-shadow:0 1px 5px rgba(0,0,0,.15)}
.card-media{height:193px}
.card h3{font-size:19px;font-weight:400;color:var(--title-blue);margin:24px 20px 10px}
.card p{font-size:11px;line-height:18px;color:var(--muted);margin:0 20px}
.btn-light{display:inline-block;background:#e6e6e6;color:#444;font-size:11px;padding:10px 20px}
.card .btn-light{position:absolute;left:20px;top:340px}
.chev{position:absolute}

.banner{position:absolute;top:1506px;left:0;width:1200px;height:399px;background:linear-gradient(90deg,#2a5a6b 0%,#5f97a6 40%,#2e6b78 70%,#184452 100%)}
.banner h2{position:absolute;right:132px;top:66px;text-align:right;color:#fff;font-size:31px;font-weight:400;line-height:42px;text-transform:uppercase}
.banner .btn-light{position:absolute;right:132px;top:160px;background:#fff}

.researches{position:absolute;top:1905px;left:0;width:1200px;height:609px}
.researches .section-title{color:var(--green);margin-top:70px}
.research{position:absolute;top:132px;width:458px}
.research-media{height:281px}
.research h3{font-size:16px;font-weight:400;color:#222;margin-top:14px}
.research p{font-size:10.5px;line-height:16px;color:var(--muted);margin-top:4px}
.research .more{display:inline-block;margin-top:6px;font-size:10.5px;color:var(--title-blue);text-decoration:underline}

.join{position:absolute;top:2514px;left:0;width:1200px;height:239px;background:var(--blue);text-align:center;color:#fff}
.join h2{font-size:31px;font-weight:400;margin-top:56px}
.join p{font-size:16px;margin-top:4px}
.btn-register{display:inline-block;margin-top:16px;background:#fff;color:var(--blue);font-size:14px;font-weight:600;padding:10px 14px}

.site-footer{position:absolute;top:2753px;left:0;width:1200px;height:321px;background:var(--footer);color:var(--footer-text)}
.footer-col{position:absolute;top:50px}
.footer-col h4{color:#fff;font-size:15px;font-weight:600;text-transform:uppercase;height:20px;line-height:20px;margin-bottom:18px}
.footer-col li{list-style:none;font-size:11.5px;line-height:26px}
.footer-col.sub{top:88px}
.newsletter-field{width:208px;height:40px;background:#fff;display:flex;align-items:center;justify-content:space-between;padding:0 14px;color:#333;font-size:12px}
.newsletter-note{font-size:11px;margin-top:12px}
.footer-rule{position:absolute;left:132px;top:196px;width:936px;height:1px;background:#4e4e4e}
.lang{position:absolute;left:132px;top:236px;width:98px;height:42px;border:1px solid #bbb;color:#fff;font-size:12px;display:flex;align-items:center;gap:8px;padding-left:16px}
.social{position:absolute;right:132px;top:248px;display:flex;gap:34px}
.social span{width:20px;height:20px;border-radius:50%;background:#fff;display:block}

.copyright{position:absolute;top:3074px;left:0;width:1200px;height:78px;text-align:center;font-size:12px;color:#333;line-height:78px}
</style>
</head>
<body>

<header class="site-header">
  <div class="brand">Marwick Biomedical Research Institute</div>
  <div class="header-actions">
    <a class="btn-top btn-login" href="#">
      <svg width="12" height="12" viewBox="0 0 12 12"><path d="M1 5h6V2l4 4-4 4V7H1z" fill="#fff"/></svg>MEMBER LOGIN</a>
    <a class="btn-top btn-donate" href="#">$ DONATE NOW</a>
  </div>
</header>

<nav class="main-nav">
  <ul>
    <li class="active">Home</li><li>About Us</li><li>Services</li><li>Research</li><li>Training</li><li>Join With Us</li><li>Contact Us</li><li>Blog</li>
  </ul>
</nav>

<section class="hero" role="img" aria-label="Photo of a doctor's hand gently holding a patient's hand">
  <span class="slider-arrow" style="left:0;top:214px"><svg width="12" height="12" viewBox="0 0 12 12"><path d="M8 2L4 6l4 4" stroke="#fff" stroke-width="2" fill="none"/></svg></span>
  <span class="slider-arrow" style="right:0;top:214px"><svg width="12" height="12" viewBox="0 0 12 12"><path d="M4 2l4 4-4 4" stroke="#fff" stroke-width="2" fill="none"/></svg></span>
</section>

<section class="welcome">
  <h1 class="section-title">Welcome to MBRI</h1>
  <p>Vivamus porta arcu mi, aliquet dictum nulla interdum quis. Donec quis ex semper, consequat ligula at, efficitur lacus. Phasellus elementum lacinia quam non pellentesque. Aliquam malesuada eros sit amet turpis scelerisque maximus. Maecenas lobortis iaculis efficitur. Nulla facilisi. Vestibulum pharetra diam ex, in posuere purus efficitur ac. Mauris placerat eros lorem, vel egestas mi eleifend eget. Donec a nisl vel ante tristique mollis nec quis est. Praesent accumsan nunc a condimentum volutpat. Sed quis metus nibh.</p>
</section>

<section class="services">
  <h2 class="section-title">Services</h2>
  <svg class="chev" style="left:48px;top:280px" width="16" height="28" viewBox="0 0 16 28"><path d="M13 2L3 14l10 12" stroke="#999" stroke-width="2" fill="none"/></svg>
  <svg class="chev" style="right:48px;top:280px" width="16" height="28" viewBox="0 0 16 28"><path d="M3 2l10 12L3 26" stroke="#999" stroke-width="2" fill="none"/></svg>

  <article class="card" style="left:132px">
    <div class="card-media" role="img" aria-label="Photo of a medical report on a clinic monitor" style="background:linear-gradient(135deg,#4a7a8c,#b9c9cf 60%,#7a5a6a)"></div>
    <h3>Cutting-edge research</h3>
    <p>Phasellus congue dapibus sapien eu tincidunt. Duis congue mauris nec tortor elementum, scelerisque posuere felis placerat. In a ligula eu nisi sodales sollicitudin. Curabitur dignissim.</p>
    <a class="btn-light" href="#">Read more</a>
  </article>
  <article class="card" style="left:452px">
    <div class="card-media" role="img" aria-label="Photo of a hand touching a digital health interface" style="background:linear-gradient(135deg,#d8e3ea,#eef3f6 50%,#c9d8e2)"></div>
    <h3>Innovative Technologies</h3>
    <p>Phasellus congue dapibus sapien eu tincidunt. Duis congue mauris nec tortor elementum, scelerisque posuere felis placerat. In a ligula eu nisi sodales sollicitudin. Curabitur dignissim.</p>
    <a class="btn-light" href="#">Read more</a>
  </article>
  <article class="card" style="left:771px">
    <div class="card-media" role="img" aria-label="Photo of a stethoscope lying on a health report" style="background:linear-gradient(135deg,#f1f4f7,#dfe8ef 60%,#e9eef2)"></div>
    <h3>Worldwide Partnerships</h3>
    <p>Phasellus congue dapibus sapien eu tincidunt. Duis congue mauris nec tortor elementum, scelerisque posuere felis placerat. In a ligula eu nisi sodales sollicitudin. Curabitur dignissim.</p>
    <a class="btn-light" href="#">Read more</a>
  </article>
</section>

<section class="banner" role="img" aria-label="Photo of a clinician using a tablet in a hospital">
  <h2>Integer sapien felis<br>sodales ut lacus</h2>
  <a class="btn-light" href="#">Read more</a>
</section>

<section class="researches">
  <h2 class="section-title">Researches</h2>
  <svg class="chev" style="left:48px;top:312px" width="16" height="28" viewBox="0 0 16 28"><path d="M13 2L3 14l10 12" stroke="#999" stroke-width="2" fill="none"/></svg>
  <svg class="chev" style="right:48px;top:312px" width="16" height="28" viewBox="0 0 16 28"><path d="M3 2l10 12L3 26" stroke="#999" stroke-width="2" fill="none"/></svg>

  <article class="research" style="left:132px">
    <div class="research-media" role="img" aria-label="Illustration of a doctor with floating medical icons" style="background:linear-gradient(135deg,#e9f4fb,#bfe0f3 55%,#f2f6f9)"></div>
    <h3>Aenean facilisis tincidunt lectus, id dictum nisi</h3>
    <p>Vivamus efficitur ex condimentum, malesuada eros eget, feugiat nibh. Sed tellus ex, imperdiet eget gravida sit amet, volutpat eget turpis. In nec ultricies est. Etiam mattis augue vehicula odio posuere, sit amet tempus lectus luctus. Nulla facilisi.</p>
    <a class="more" href="#">READ MORE</a>
  </article>
  <article class="research" style="left:609px">
    <div class="research-media" role="img" aria-label="Photo of a nurse preparing a patient for a scanner" style="background:linear-gradient(135deg,#eceff2,#c9d3dc 55%,#8fa3b5)"></div>
    <h3>Phasellus nisl est, condimentum vitae faucibus</h3>
    <p>Vivamus efficitur ex condimentum, malesuada eros eget, feugiat nibh. Sed tellus ex, imperdiet eget gravida sit amet, volutpat eget turpis. In nec ultricies est. Etiam mattis augue vehicula odio posuere, sit amet tempus lectus luctus. Nulla facilisi.</p>
    <a class="more" href="#">READ MORE</a>
  </article>
</section>

<section class="join">
  <h2>JOIN WITH US</h2>
  <p>Aenean sit amet suscipit leo. Aenean commodo luctus ipsum, at pulvinar ipsum rutrum ut</p>
  <a class="btn-register" href="#">REGISTER NOW</a>
</section>

<footer class="site-footer">
  <div class="footer-col" style="left:132px">
    <h4>Newsletter</h4>
    <div class="newsletter-field">Email
      <svg width="16" height="12" viewBox="0 0 16 12"><rect x="0" y="0" width="16" height="12" fill="#333"/><path d="M0 0l8 6 8-6" stroke="#fff" stroke-width="1.4" fill="none"/></svg>
    </div>
    <p class="newsletter-note">Curabitur eu erat dignissim varius</p>
  </div>
  <div class="footer-col" style="left:428px">
    <h4>Help</h4>
    <ul><li>Customer Service</li><li>Live Chat</li><li>555.014.2290</li></ul>
  </div>
  <div class="footer-col" style="left:627px">
    <h4>Links</h4>
    <ul><li>Home</li><li>About Us</li><li>Services</li></ul>
  </div>
  <div class="footer-col sub" style="left:723px">
    <ul><li>Research</li><li>Training</li><li>Join With Us</li></ul>
  </div>
  <div class="footer-col sub" style="left:819px">
    <ul><li>Contact Us</li><li>Blog</li></ul>
  </div>
  <div class="footer-col" style="left:982px">
    <h4>Subscribe</h4>
    <ul><li>Emails</li><li>News</li><li>Unsubscribe</li></ul>
  </div>
  <div class="footer-rule"></div>
  <div class="lang">
    <svg width="12" height="12" viewBox="0 0 12 12"><circle cx="6" cy="6" r="6" fill="#fff"/></svg>English
  </div>
  <div class="social">
    <span aria-label="Social link 1"></span><span aria-label="Social link 2"></span><span aria-label="Social link 3"></span><span aria-label="Social link 4"></span><span aria-label="Social link 5"></span>
  </div>
</footer>

<div class="copyright">Copyright © 2017 MBRI.  All rights reserved.</div>

</body>
</html>
```